Business Card Design

New business card design

Target Market(s)

Residential & Commercial Property Managers

Industry/Entity Type

Plumbing Services

Contact Information for Business Card

Name - Rowan Keddle, title - Director, Phone Number - 0431 286 517, email - rowan@tbk-plumbing.com.au, Company ABN - 73 215 904 386,

Font styles to use
Sans Serif

Colors
0054AA
0677BA
7BADD7
CADEEF
E8F1F8

```html
<!DOCTYPE html>
<html lang="en">
<head>
<meta charset="utf-8">
<title>TBK Plumbing Services – Business Card</title>
<link rel="stylesheet" href="https://fonts.googleapis.com/css2?family=Montserrat:wght@300;400;700&display=swap">
<style>
  :root {
    --stage: #ecedef;
    --ink: #1e242b;
    --charcoal: #1d232a;
    --sky: #2aa7df;
    --paper: #ffffff;
    --back-text: #3a424b;
  }
  * { box-sizing: border-box; margin: 0; padding: 0; }
  html, body { width: 1200px; height: 912px; overflow: hidden; }
  body {
    background: var(--stage);
    font-family: "Montserrat", sans-serif;
    display: flex;
    flex-direction: column;
    align-items: center;
    justify-content: center;
    gap: 40px;
  }
  .card {
    position: relative;
    width: 700px;
    height: 400px;
    border-radius: 22px;
    overflow: hidden;
    box-shadow: 0 8px 24px rgba(0,0,0,.18);
  }
  .card--back { background: var(--charcoal); }
  .card--front { background: var(--paper); }

  .brand {
    position: absolute;
    left: 0;
    right: 0;
    display: flex;
    align-items: center;
    justify-content: center;
    gap: 14px;
    font-weight: 400;
    white-space: nowrap;
  }
  .brand__dot {
    width: 18px; height: 18px;
    border-radius: 50%;
    background: var(--sky);
    flex: none;
  }
  .card--back .brand {
    top: 170px;
    color: var(--back-text);
    font-size: 40px;
    letter-spacing: 3px;
  }
  .card--front .brand {
    top: 84px;
    padding-left: 60px;
    color: var(--ink);
    font-size: 34px;
    letter-spacing: 2px;
  }

  .person {
    position: absolute;
    right: 322px;
    top: 198px;
    text-align: right;
    white-space: nowrap;
  }
  .person__name {
    color: var(--sky);
    font-weight: 700;
    font-size: 32px;
    line-height: 1.05;
  }
  .person__role {
    color: var(--ink);
    font-weight: 400;
    font-size: 19px;
    margin-top: 2px;
  }
  .divider {
    position: absolute;
    left: 395px; top: 190px;
    width: 1px; height: 92px;
    background: var(--sky);
  }
  .contact {
    position: absolute;
    left: 412px; top: 184px;
    list-style: none;
    font-size: 16px;
    color: var(--ink);
    line-height: 1.7;
  }
  .contact li { display: flex; align-items: center; gap: 8px; white-space: nowrap; }
  .contact__label { color: var(--sky); }
  .contact__icon { width: 14px; height: 14px; flex: none; }
  .swoosh { position: absolute; left: 0; bottom: 0; width: 700px; height: 104px; }
</style>
</head>
<body>

<section class="card card--back" aria-label="Card back">
  <div class="brand"><span class="brand__dot"></span>TBK Plumbing Services</div>
</section>

<section class="card card--front" aria-label="Card front">
  <div class="brand"><span class="brand__dot"></span>TBK Plumbing Services</div>

  <div class="person">
    <p class="person__name">Rowan Keddle</p>
    <p class="person__role">Director</p>
  </div>

  <div class="divider"></div>

  <ul class="contact">
    <li><span class="contact__label">ABN</span> - 73 215 904 386</li>
    <li>
      <svg class="contact__icon" viewBox="0 0 24 24" aria-hidden="true"><path fill="#2aa7df" d="M6.6 10.8a15 15 0 0 0 6.6 6.6l2.2-2.2c.3-.3.7-.4 1-.2 1.1.4 2.3.6 3.6.6.6 0 1 .4 1 1V20c0 .6-.4 1-1 1A17 17 0 0 1 3 4c0-.6.4-1 1-1h3.5c.6 0 1 .4 1 1 0 1.3.2 2.5.6 3.6.1.3 0 .7-.2 1z"/></svg>
      0431 286 517
    </li>
    <li>
      <svg class="contact__icon" viewBox="0 0 24 24" aria-hidden="true"><path fill="#2aa7df" d="M2 5h20v14H2z"/><path fill="none" stroke="#fff" stroke-width="1.6" d="M2 5l10 8 10-8"/></svg>
      rowan@tbk-plumbing.com.au
    </li>
  </ul>

  <svg class="swoosh" viewBox="0 0 700 104" preserveAspectRatio="none" aria-hidden="true">
    <path d="M0 104 L0 84 Q360 80 700 16 L700 104 Z" fill="var(--charcoal)"/>
    <path d="M40 82 Q380 64 700 4" fill="none" stroke="var(--sky)" stroke-width="4"/>
  </svg>
</section>

</body>
</html>
```